A layout of a webpage for oil trade platform

I would like to have a desgin of one page webpage (with section scrollling dowin) that woulf present the new product i.e. oil trade platform for wholesale buyers and sellers.
Layout should consist of the sections similar to the given at: https://porada.leczmypol.pl/panel-planowania-spotkan
However oil industy require more colors and more photo stories than here for doctor.
I. I woul imagine at first below menu a slider with brueg information about the product and its advantages with "more" button next to the prict screen of our platform on different displays (PC and mobile).
II. Bellow the slider I would imagine icons correspoing to the advantages of that plaftorm:
1. Purchase/sale process automation 24/7
2. Access to the best deals
3. Electronic offerings and orderings
4. Transaction status monitoring
5. Data and transaction security
II A) (optional):
In near future we would like to prepare a short video presenation. Hence please prepare a place to display that element here.
At the moment alternatvily please prepare a How it works section that would explan the platform operating process
III. Next secion is about benefits for Oil Purchaser
It can be done either by icons of by text and corresponding grahip for while section.
Benefits:
- Access to cheaper oil
- Convenience of online orders
- Possibility to compare prices on the market
- Transaction history
- Order status monitoring
- Seccurity and transparency of purchase
IV. Next seciont is about benefits for Oil Seller
Benefits:
- New sale channel
- Attracting new clients
- More oil sold
- Transaction security
- Possibility to integrate with distribution infrastructure and logistits for more efficient automation.
V. Contact form
VI. Footer
I would need a layout that that will correspond to the very dynamic logo but I would expect also a clean form, smoth and modern. It has to be proffessional layout with more corporate character.
It can use a paralax features if needed.

```html
<!DOCTYPE html>
<html lang="en">
<head>
<meta charset="utf-8">
<title>Crudexa – Oil Trade Platform</title>
<link href="https://fonts.googleapis.com/css2?family=Ubuntu:wght@400;500;700&family=Open+Sans:wght@400;600;700&display=swap" rel="stylesheet">
<style>
:root{
  --orange:#f26522;
  --orange-light:#f7893a;
  --navy:#17295c;
  --navy-2:#24408c;
  --ink:#2a2a2a;
  --text:#555b66;
  --muted:#8a8f98;
  --line:#d9dce1;
  --soft:#f4f4f5;
  --white:#ffffff;
  --device:#0d0d0f;
}
*{box-sizing:border-box;margin:0;padding:0}
html,body{width:1200px;height:3285px;overflow:hidden}
body{font-family:"Open Sans",Arial,sans-serif;color:var(--text);background:var(--white);position:relative}
section,header,footer{position:absolute;left:0;width:1200px}
.abs{position:absolute}
h1,h2,h3{font-family:"Ubuntu","Open Sans",sans-serif;font-weight:500;color:var(--ink)}
.btn{position:absolute;display:flex;align-items:center;justify-content:center;gap:8px;color:var(--white);
  background:linear-gradient(180deg,var(--orange-light),var(--orange));font-weight:600;font-size:14px;
  text-transform:uppercase;letter-spacing:.4px;box-shadow:0 2px 4px rgba(0,0,0,.18)}

/* hero */
.hero{top:0;height:668px;background:radial-gradient(ellipse at 30% 40%,var(--navy-2),var(--navy) 70%);overflow:hidden}
.brand{position:absolute;display:flex;align-items:center;gap:12px;font-family:"Ubuntu",sans-serif;font-weight:500}
.brand .dot{width:34px;height:34px;border-radius:50%;background:var(--orange)}
.hero .brand{left:75px;top:36px;font-size:32px;color:var(--white)}
.nav{position:absolute;top:46px;left:414px;display:flex;height:35px;align-items:center}
.nav a{color:var(--white);text-decoration:none;font-size:13px;text-transform:uppercase;font-weight:600;margin-right:31px}
.nav a.active{background:var(--orange);padding:0 20px;height:35px;line-height:35px;margin-right:21px}
.hero h1{position:absolute;left:75px;top:250px;width:520px;color:var(--white);font-size:33px;line-height:40px}
.hero p{position:absolute;left:75px;top:348px;width:500px;color:#dfe6f5;font-size:18px;line-height:26px}
.hero .btn{left:75px;top:458px;width:151px;height:50px;font-size:16px}
.screen{background:linear-gradient(160deg,#eef1f5,#dfe4ea)}
.screen .side{position:absolute;left:0;top:0;bottom:0;background:#2f3440}

/* features */
.features{top:668px;height:193px;background:var(--white)}
.feature{position:absolute;top:28px;width:210px;text-align:center;font-size:15px;font-weight:600;color:#3b4150;line-height:21px}
.feature svg{display:block;margin:0 auto 10px}

/* how */
.how{top:861px;height:427px;background:var(--soft)}
.how h2{position:absolute;left:613px;top:86px;font-size:27px}
.how p{position:absolute;left:613px;top:136px;width:515px;font-size:13.5px;line-height:24px;color:var(--muted)}
.how .btn{left:613px;top:282px;width:243px;height:57px;font-size:14px}

/* benefits */
.benefits{height:525px}
.buyer{top:1288px;background:var(--white)}
.seller{top:1813px;height:530px;background:var(--soft)}
.benefits h2{position:absolute;font-size:27px}
.list{position:absolute;list-style:none}
.list li{display:flex;align-items:center;gap:30px;font-size:15px;font-weight:600;color:#4a4f5a;height:60px;line-height:22px}
.list svg{flex:none}
.photo{position:absolute}

/* contact */
.contact{top:2343px;height:504px;background:var(--white)}
.contact h2{position:absolute;width:1200px;top:67px;text-align:center;font-size:28px}
.contact .lead{position:absolute;width:1200px;top:128px;text-align:center;font-size:14px;color:#666}
.field{position:absolute;border:1px solid var(--line);background:var(--white);font-size:13px;color:#666;padding:14px 12px}
.contact .btn{left:480px;top:386px;width:240px;height:55px}

/* footer */
.footer{top:2847px;height:438px;background:var(--soft)}
.footer .brand{left:75px;top:56px;font-size:30px;color:var(--ink)}
.footer .brand .dot{width:30px;height:30px}
.addr{position:absolute;left:75px;top:132px;font-size:15px;line-height:28px;color:#555}
.flink{position:absolute;left:75px;display:flex;align-items:center;gap:18px;font-size:15px;color:var(--orange)}
.socials{position:absolute;left:75px;top:3140px;display:flex;gap:18px}
.fcol{position:absolute;top:61px}
.fcol h4{font-size:14px;font-weight:700;color:#333;text-transform:uppercase;margin-bottom:14px;letter-spacing:.3px}
.fcol li{list-style:none;font-size:15px;color:#555;line-height:30.7px}
.news input{display:block;width:243px;height:44px;border:1px solid var(--line);padding:0 12px;font:14px "Open Sans",sans-serif;color:#777;margin-bottom:8px}
.news .btn{position:relative;margin-left:153px;width:90px;height:42px;font-size:14px}
.rule{position:absolute;left:75px;top:340px;width:1050px;height:1px;background:#dfe1e5}
.copy{position:absolute;top:380px;width:1200px;text-align:center;font-size:13px;color:#888}
</style>
</head>
<body>

<header class="hero">
  <div class="brand"><span class="dot"></span>Crudexa</div>
  <nav class="nav">
    <a class="active">Home</a><a>About us</a><a>Services</a><a>How it works</a><a>Benefits</a><a>Blog</a><a>Contact us</a>
  </nav>
  <h1>Nam fermentum vestibulum amet turpis tincidunt.</h1>
  <p>Aliquam molestie, mi et imperdiet euismod, dui purus auctor tellus, et interdum lacus lectus et ante dignissim lectus vitae.</p>
  <a class="btn">More <svg width="10" height="14" viewBox="0 0 10 14"><path d="M2 1l6 6-6 6" stroke="#fff" stroke-width="2.5" fill="none"/></svg></a>

  <!-- desktop monitor -->
  <div class="abs" style="left:580px;top:180px;width:580px;height:420px;background:var(--device);border-radius:14px"></div>
  <div class="abs screen" role="img" aria-label="Platform order dashboard on desktop" style="left:600px;top:200px;width:540px;height:380px">
    <div class="side" style="width:110px"></div>
  </div>
  <div class="abs" style="left:820px;top:600px;width:100px;height:50px;background:#1b1b1e"></div>
  <div class="abs" style="left:770px;top:650px;width:200px;height:10px;background:#2a2a2e;border-radius:4px"></div>
  <!-- laptop -->
  <div class="abs" style="left:460px;top:429px;width:336px;height:224px;background:var(--device);border-radius:10px 10px 0 0"></div>
  <div class="abs screen" role="img" aria-label="Platform order dashboard on laptop" style="left:474px;top:443px;width:308px;height:200px">
    <div class="side" style="width:54px"></div>
  </div>
  <div class="abs" style="left:449px;top:653px;width:357px;height:14px;background:#c9ccd2;border-radius:0 0 12px 12px"></div>
  <!-- phone -->
  <div class="abs" style="left:1069px;top:429px;width:74px;height:228px;background:var(--device);border-radius:14px"></div>
  <div class="abs screen" role="img" aria-label="Platform order list on phone" style="left:1075px;top:456px;width:62px;height:172px"></div>
</header>

<section class="features">
  <div class="feature" style="left:75px">
    <svg width="60" height="60" viewBox="0 0 60 60" fill="none" stroke="#2c3e70" stroke-width="2"><circle cx="30" cy="30" r="27"/><circle cx="30" cy="30" r="17"/><path d="M30 20v10h8"/></svg>
    Purchase/sale process<br>automation 24/7</div>
  <div class="feature" style="left:283px">
    <svg width="60" height="60" viewBox="0 0 60 60" fill="none" stroke="#2c3e70" stroke-width="2"><rect x="8" y="26" width="10" height="26"/><path d="M18 28l10-16c2-4 8-2 7 3l-2 9h14c3 0 5 3 4 6l-5 18c-1 3-3 4-5 4H18"/></svg>
    Access to the best<br>deals</div>
  <div class="feature" style="left:495px">
    <svg width="60" height="60" viewBox="0 0 60 60" fill="none" stroke="#2c3e70" stroke-width="2"><rect x="4" y="4" width="52" height="52" rx="6"/><path d="M18 42l4-12 18-18 8 8-18 18z M18 42l12-4"/></svg>
    Electronic offerings<br>and orderings</div>
  <div class="feature" style="left:705px">
    <svg width="70" height="60" viewBox="0 0 70 60" fill="none" stroke="#2c3e70" stroke-width="2"><rect x="12" y="10" width="46" height="32" rx="2"/><path d="M4 48h62l-4 6H8z"/></svg>
    Transaction status<br>monitoring</div>
  <div class="feature" style="left:911px">
    <svg width="60" height="60" viewBox="0 0 60 60" fill="none" stroke="#2c3e70" stroke-width="2"><path d="M30 4l22 8v16c0 14-10 24-22 28C18 52 8 42 8 28V12z"/><path d="M30 12v38"/></svg>
    Data and transaction<br>security</div>
</section>

<section class="how">
  <div class="abs" style="left:75px;top:43px;width:483px;height:340px;background:#2f3138;border-radius:12px"></div>
  <div class="abs" role="img" aria-label="Video presentation of the platform dashboard with trading chart" style="left:95px;top:63px;width:443px;height:300px;background:linear-gradient(180deg,#f1f3f6 0 12%,#dfe7d8 40%,#9bc36b 70%,#e9ecef 72%)">
    <div class="abs" style="left:0;top:0;bottom:0;width:80px;background:#2d3340"></div>
    <svg class="abs" style="left:184px;top:113px" width="74" height="74" viewBox="0 0 74 74"><circle cx="37" cy="37" r="33" fill="rgba(0,0,0,.35)" stroke="#fff" stroke-width="4"/><path d="M29 22l24 15-24 15z" fill="#fff"/></svg>
  </div>
  <h2>How it Works</h2>
  <p>Aliquam molestie, mi et imperdiet euismod, dui purus auctor tellus, et interdum lacus lectus et ante. Sed accumsan sollicitudin sapien, sit amet adipiscing turpis gravida ac. In congue, neque ac lobortis volutpat, libero mauris varius mi, vitae suscipit ipsum ligula vitae risus.</p>
  <a class="btn">See how it works</a>
</section>

<section class="benefits buyer">
  <h2 style="left:75px;top:62px">Benefits for Oil Purchaser</h2>
  <ul class="list" style="left:80px;top:123px">
    <li><svg width="36" height="36" viewBox="0 0 36 36" fill="none" stroke="var(--orange)" stroke-width="3"><circle cx="10" cy="10" r="7"/><path d="M15 15l16 16M25 25l4-4M21 21l4-4"/></svg>Access to cheaper oil</li>
    <li><svg width="36" height="36" viewBox="0 0 36 36" fill="none" stroke="var(--orange)" stroke-width="3"><rect x="3" y="7" width="24" height="24" rx="3"/><path d="M14 22l2-6 14-14 4 4-14 14z"/></svg>Convenience of online orders</li>
    <li><svg width="36" height="36" viewBox="0 0 36 36" fill="none" stroke="var(--orange)" stroke-width="3"><path d="M4 12h26l-6-6M32 24H6l6 6"/></svg>Possibility to compare prices on the market</li>
    <li><svg width="36" height="36" viewBox="0 0 36 36" fill="none" stroke="var(--orange)" stroke-width="3"><circle cx="18" cy="18" r="14"/><path d="M18 10v9h7"/></svg>Transaction history</li>
    <li><svg width="36" height="36" viewBox="0 0 36 36" fill="none" stroke="var(--orange)" stroke-width="3"><rect x="6" y="6" width="24" height="17" rx="1"/><path d="M2 28h32"/></svg>Order status monitoring</li>
    <li><svg width="36" height="36" viewBox="0 0 36 36"><path d="M18 2l14 5v10c0 9-6 15-14 18C10 32 4 26 4 17V7z" fill="var(--orange)"/><path d="M18 6v25" stroke="#fff" stroke-width="2"/></svg>Security and transparency of purchase</li>
  </ul>
  <div class="photo" role="img" aria-label="Photo of an oil tanker at a container port at sunset" style="left:613px;top:0;width:587px;height:525px;background:linear-gradient(180deg,#1d3f6e 0%,#4a6f98 35%,#e4a35a 62%,#b8642a 75%,#2a2320 100%)"></div>
</section>

<section class="benefits seller">
  <div class="photo" role="img" aria-label="Photo of an illuminated oil refinery at sunrise" style="left:0;top:0;width:587px;height:530px;background:linear-gradient(180deg,#f2c776 0%,#e8b25a 30%,#a37a54 60%,#4a3f52 100%)"></div>
  <h2 style="left:635px;top:88px">Benefits for Oil Seller</h2>
  <ul class="list" style="left:640px;top:132px">
    <li><svg width="36" height="36" viewBox="0 0 36 36" fill="var(--orange)"><rect x="13" y="3" width="10" height="9"/><rect x="2" y="24" width="10" height="9"/><rect x="13" y="24" width="10" height="9"/><rect x="24" y="24" width="10" height="9"/><path d="M17 12h2v6h11v6h-2v-4H19v4h-2v-4H8v4H6v-6h11z"/></svg>New sale channel</li>
    <li><svg width="36" height="36" viewBox="0 0 36 36" fill="var(--orange)"><circle cx="18" cy="11" r="6"/><circle cx="7" cy="14" r="4"/><circle cx="29" cy="14" r="4"/><path d="M8 32c0-8 4-13 10-13s10 5 10 13zM0 30c0-6 3-9 7-9 2 0 3 1 3 1-2 2-3 5-3 8zM36 30c0-6-3-9-7-9-2 0-3 1-3 1 2 2 3 5 3 8z"/></svg>Attracting new clients</li>
    <li><svg width="36" height="36" viewBox="0 0 36 36"><path d="M18 3C14 11 8 17 8 23a10 10 0 0 0 20 0c0-6-6-12-10-20z" fill="var(--orange)"/></svg>More oil sold</li>
    <li><svg width="36" height="36" viewBox="0 0 36 36"><path d="M11 16v-5a7 7 0 0 1 14 0v5" stroke="var(--orange)" stroke-width="3" fill="none"/><rect x="7" y="16" width="22" height="17" rx="2" fill="var(--orange)"/></svg>Transaction security</li>
    <li style="height:80px"><svg width="36" height="36" viewBox="0 0 36 36" fill="none" stroke="var(--orange)" stroke-width="3"><circle cx="13" cy="20" r="8"/><circle cx="13" cy="20" r="3"/><path d="M13 9v-3M13 34v-3M2 20h3M21 20h3M5 12l2 2M19 26l2 2M5 28l2-2M19 14l2-2"/><circle cx="28" cy="9" r="4"/></svg><span style="width:400px">Possibility to integrate with distribution infrastructure and logistits for more efficient automation.</span></li>
  </ul>
</section>

<section class="contact">
  <h2>Contact Us</h2>
  <div class="lead">Vestibulum vel metus sit amet turpis bibendum tincidunt vel sit amet quam</div>
  <div class="field" style="left:164px;top:191px;width:423px;height:46px">Name</div>
  <div class="field" style="left:164px;top:246px;width:423px;height:46px">Email Address</div>
  <div class="field" style="left:164px;top:300px;width:423px;height:46px">Phone No</div>
  <div class="field" style="left:613px;top:191px;width:423px;height:155px">Message</div>
  <a class="btn">See how it works</a>
</section>

<footer class="footer">
  <div class="brand"><span class="dot"></span>Crudexa</div>
  <div class="addr">412 Harbour Lane<br>Aberdeen, AB11 5QT</div>
  <div class="flink" style="top:194px"><svg width="14" height="12" viewBox="0 0 14 12"><rect width="14" height="12" rx="1" fill="var(--orange)"/><path d="M1 2l6 5 6-5" stroke="#fff" fill="none"/></svg>info@crudexa-trade.com</div>
  <div class="flink" style="top:227px"><svg width="12" height="16" viewBox="0 0 12 16"><path d="M6 0a6 6 0 0 0-6 6c0 4 6 10 6 10s6-6 6-10a6 6 0 0 0-6-6z" fill="var(--orange)"/><circle cx="6" cy="6" r="2" fill="#fff"/></svg>Map Location</div>
  <div class="abs" style="left:75px;top:284px;display:flex;gap:18px">
    <span style="width:16px;height:16px;border-radius:50%;background:#9aa0a8"></span>
    <span style="width:16px;height:16px;border-radius:50%;background:#9aa0a8"></span>
    <span style="width:16px;height:16px;border-radius:50%;background:#9aa0a8"></span>
    <span style="width:16px;height:16px;border-radius:50%;background:#9aa0a8"></span>
    <span style="width:16px;height:16px;border-radius:50%;background:#9aa0a8"></span>
    <span style="width:16px;height:16px;border-radius:50%;background:#9aa0a8"></span>
  </div>
  <div class="fcol" style="left:379px"><h4>Site Map</h4><ul><li>Home</li><li>About Us</li><li>Services</li><li>How it Works</li><li>Benefits</li><li>Blog</li><li>Contact Us</li></ul></div>
  <div class="fcol" style="left:618px"><h4>Resources</h4><ul><li>Aliquam molestie</li><li>Perdiet euismod</li><li>Dui purus auctor tellus</li><li>Dum lacus lectus</li></ul></div>
  <div class="fcol news" style="left:883px"><h4>Newsletter Sign Up</h4><input value="Enter Email Address" readonly><a class="btn">Sign up</a></div>
  <div class="rule"></div>
  <div class="copy">Copyright © 2017. Crudexa Trade. All Right Reserved</div>
</footer>

</body>
</html>
```